Four in One (Flexible infographic for Content Management Industry)

See attachment.
A graphic depicting 4 products, where each can stand on its own and each can be combined with others, but where, if all are taken together, the best result is achieved (the "super product").
Intended use is web. See attached file as an example.
The most basic idea is as the attached diagram shows, where 4 rectangles are arranged in a quadrangle, with a middle rectangle in the center representing the combined 4 products. This concept is fine except it is a bit too obvious as it stands. We are looking for either a variation of this or another concept.
The audience is technical + professional + enterprise - NOT consumers. Hence the design should be conservative in nature.
We are aware of tools like as Canva or Pictogram where such graphics are available, but we are looking for something with a bit more imagination and flexibility.
This graphic should be targeted to web sites and be delivered with vector-based (SVG) graphics.

```html
<!DOCTYPE html>
<html lang="en">
<head>
<meta charset="utf-8">
<title>Four in One – Super Product</title>
<link rel="stylesheet" href="https://fonts.googleapis.com/css2?family=Montserrat:wght@500;600;700;800&display=swap">
<style>
  :root {
    --navy: #4f6189;
    --navy-ink: #2e4066;
    --plum: #622f55;
    --plum-ink: #6b2d5c;
    --magenta: #c21d7e;
    --teal: #52a8b0;
    --orange: #f58634;
    --ink: #2b2b2b;
    --head-bg: #e6e7e8;
    --desc-bg: #f6f6f6;
    --list-bg: #ffffff;
    --rule: #2b2b2b;
    --band: #e6e7e8;
    --band-text: #c0c0c1;
  }
  * { box-sizing: border-box; margin: 0; padding: 0; }
  html, body { width: 1200px; height: 713px; overflow: hidden; background: #fff; }
  body { font-family: "Montserrat", sans-serif; color: var(--ink); position: relative; }

  .product-band {
    position: absolute; left: 52px; top: 487px; width: 1103px; height: 195px;
    background: var(--band);
  }
  .product-band__name {
    position: absolute; left: 70px; top: 22px; width: 945px;
    font-weight: 800; font-size: 128px; letter-spacing: -1px; line-height: 1;
    color: var(--band-text); white-space: nowrap; word-spacing: 22px;
  }

  .offer {
    position: absolute; top: 35px; width: 258px; height: 437px;
    display: flex; flex-direction: column;
  }
  .offer--docs { left: 52px; --accent: var(--navy); --title: var(--navy-ink); }
  .offer--security { left: 329px; --accent: var(--plum); --title: var(--plum-ink); }
  .offer--digital { left: 613px; --accent: var(--teal); --title: var(--ink); }
  .offer--erp { left: 896px; --accent: var(--orange); --title: var(--ink); }

  .offer__cap { height: 8px; background: var(--accent); }
  .offer__head {
    height: 152px; background: var(--head-bg); border-bottom: 3px solid var(--rule);
    display: flex; flex-direction: column; align-items: center; padding-top: 10px;
  }
  .offer__icon { width: 64px; height: 64px; }
  .offer__title {
    margin-top: 6px; font-weight: 800; font-size: 25px; line-height: 26px;
    color: var(--title); text-align: center; white-space: nowrap;
  }
  .offer__desc {
    height: 148px; background: var(--desc-bg); padding: 14px 12px 0;
    font-weight: 600; font-size: 14px; line-height: 18px; text-align: center;
  }
  .offer--erp .offer__desc { text-align: left; padding-left: 6px; }
  .offer__list {
    flex: 1; background: var(--list-bg); list-style: none;
    padding: 16px 0 0 18px; font-weight: 600; font-size: 11.5px; line-height: 14px;
    border-left: 1px solid #eee; border-right: 1px solid #eee;
  }
  .offer__list li { position: relative; padding-left: 14px; white-space: nowrap; }
  .offer__list li::before {
    content: ""; position: absolute; left: 1px; top: 3px; width: 8px; height: 4px;
    border-left: 2px solid var(--ink); border-bottom: 2px solid var(--ink);
    transform: rotate(-45deg);
  }
  .offer__base { height: 17px; background: var(--accent); }
  .offer__arrow { position: absolute; left: 101px; top: 437px; width: 56px; height: 48px; }
  .offer__arrow path { fill: var(--accent); }
</style>
</head>
<body>

<div class="product-band">
  <div class="product-band__name">Super Product</div>
</div>

<section class="offer offer--docs">
  <div class="offer__cap"></div>
  <div class="offer__head">
    <svg class="offer__icon" viewBox="0 0 64 64" aria-hidden="true">
      <circle cx="32" cy="30" r="28" fill="none" stroke="var(--navy)" stroke-width="2.5"/>
      <path d="M22 14h15l7 7v25H22z" fill="none" stroke="var(--navy)" stroke-width="2"/>
      <path d="M26 24h14M26 29h14M26 34h14M26 39h14" stroke="var(--navy)" stroke-width="1.6"/>
    </svg>
    <h2 class="offer__title">Document<br>Management</h2>
  </div>
  <p class="offer__desc">Streamline document organization, access, and collaboration with easier file storage and sharing, leading to more efficient workflows .</p>
  <ul class="offer__list">
    <li>Centralized Document Control</li>
    <li>Collaborative Workspace Integration</li>
    <li>Automated Compliance Tracking</li>
    <li>Check 4</li>
  </ul>
  <div class="offer__base"></div>
  <svg class="offer__arrow" viewBox="0 0 56 48" aria-hidden="true"><path d="M14 0h28v20h14L28 48 0 20h14z"/></svg>
</section>

<section class="offer offer--security">
  <div class="offer__cap"></div>
  <div class="offer__head">
    <svg class="offer__icon" viewBox="0 0 64 64" aria-hidden="true">
      <path d="M32 4c7 6 15 8 24 8v18c0 16-12 26-24 30C20 56 8 46 8 30V12c9 0 17-2 24-8z" fill="none" stroke="var(--magenta)" stroke-width="4" stroke-linejoin="round"/>
      <path d="M21 32l8 8 15-16" fill="none" stroke="var(--magenta)" stroke-width="5" stroke-linecap="round" stroke-linejoin="round"/>
    </svg>
    <h2 class="offer__title">Security<br>and Compliance</h2>
  </div>
  <p class="offer__desc">Benefit from tailored cloud solutions, secure data storage, and expert disaster recovery planning for reliable and scalable IT operations.</p>
  <ul class="offer__list">
    <li>Custom Cloud Solutions</li>
    <li>Secure Data Storage</li>
    <li>Expert Disaster Recovery</li>
    <li>Check 4</li>
  </ul>
  <div class="offer__base"></div>
  <svg class="offer__arrow" viewBox="0 0 56 48" aria-hidden="true"><path d="M14 0h28v20h14L28 48 0 20h14z"/></svg>
</section>

<section class="offer offer--digital">
  <div class="offer__cap"></div>
  <div class="offer__head">
    <svg class="offer__icon" viewBox="0 0 64 64" aria-hidden="true">
      <g fill="none" stroke="var(--teal)" stroke-width="3.5" stroke-linecap="round">
        <path d="M4 22c16-14 40-14 56 0"/>
        <path d="M11 29c12-10 30-10 42 0"/>
        <path d="M18 36c8-6 20-6 28 0"/>
        <path d="M25 42c4-3 10-3 14 0"/>
      </g>
      <circle cx="32" cy="50" r="4.5" fill="var(--teal)"/>
    </svg>
    <h2 class="offer__title">Digital<br>Transformation</h2>
  </div>
  <p class="offer__desc">Turn scanned documents into easily searchable digital archives, boosting efficiency and accessibility.</p>
  <ul class="offer__list" style="padding-left:6px">
    <li>Instant searchable Archives with OCR</li>
    <li>Automated Document Classification</li>
    <li>TeamVault and Cloud Blob Ready</li>
    <li>Check 4</li>
  </ul>
  <div class="offer__base"></div>
  <svg class="offer__arrow" viewBox="0 0 56 48" aria-hidden="true"><path d="M14 0h28v20h14L28 48 0 20h14z"/></svg>
</section>

<section class="offer offer--erp">
  <div class="offer__cap"></div>
  <div class="offer__head">
    <svg class="offer__icon" viewBox="0 0 64 64" aria-hidden="true">
      <g fill="none" stroke="var(--orange)" stroke-width="3.5" stroke-linejoin="round">
        <path d="M20 10h28v46H20z"/>
        <path d="M14 4h28v46H14z" fill="var(--head-bg)"/>
      </g>
      <path d="M19 16h18M19 23h18M19 30h18M19 37h18M19 44h12" stroke="var(--orange)" stroke-width="3"/>
    </svg>
    <h2 class="offer__title">Enterprise<br>Resource Planning</h2>
  </div>
  <p class="offer__desc">Simplify management across finance, sales, and operations, enabling better decision-making and improved productivity.</p>
  <ul class="offer__list">
    <li>Integrated Business Processes</li>
    <li>Enhanced Decision-Making</li>
    <li>Productivity Improvement</li>
    <li>Check 4</li>
  </ul>
  <div class="offer__base"></div>
  <svg class="offer__arrow" viewBox="0 0 56 48" aria-hidden="true"><path d="M14 0h28v20h14L28 48 0 20h14z"/></svg>
</section>

</body>
</html>
```